KBT Business Cards

We require business cards for our business. We would like a matte black back to the card, with our logo centred in the middle. The front side of the card is open to design.

Target Market(s)

Clients looking for legal services (professional)

Industry/Entity Type

Legal

Contact Information for Business Card

Doran Kelbrath
Partner
Mobile: 0461 738 524
Email: doran@kbtlaw.co
Website: www.kbtlaw.co
Level 3, 118 Wendmore Street
Sydney NSW 2000

Font styles to use
Other font styles liked:
• Avenir

Colors
f04a50
ffffff
1b1b1b

Requirements
Must have
• Black back with logo included in the centre of the card.
• Our font is Avenir.

```html
<!DOCTYPE html>
<html lang="en">
<head>
<meta charset="utf-8">
<title>Kelbrath Brannock Legal – Business Card</title>
<link rel="stylesheet" href="https://fonts.googleapis.com/css2?family=Nunito+Sans:wght@400;600;800&display=swap">
<style>
  :root {
    --brand-red: #f04a50;
    --brand-red-deep: #a81f3c;
    --ink: #1b1b1b;
    --paper: #ffffff;
    --stage: #2a2a2c;
    --muted: #4a4a4a;
    --font: "Nunito Sans", "Avenir", sans-serif;
  }
  * { box-sizing: border-box; margin: 0; padding: 0; }
  html, body {
    width: 1200px; height: 960px; overflow: hidden;
    background: var(--stage);
    font-family: var(--font);
  }
  .stage { position: relative; width: 1200px; height: 960px; }
  .card {
    position: absolute; left: 285px; width: 630px; height: 360px;
    border-radius: 6px; overflow: hidden;
    box-shadow: 0 18px 40px rgba(0,0,0,.45);
  }

  /* Back */
  .card--back {
    top: 70px;
    background: radial-gradient(ellipse at 50% 40%, #262626 0%, var(--ink) 70%);
  }
  .wordmark {
    position: absolute; left: 50%; top: 150px; transform: translateX(-50%);
    display: flex; align-items: center; gap: 18px;
  }
  .wordmark__square { width: 46px; height: 46px; background: var(--brand-red); }
  .wordmark__name {
    font-weight: 800; font-size: 30px; line-height: 1; letter-spacing: .5px;
    text-transform: uppercase; color: var(--paper); white-space: nowrap;
  }
  .card--back .site {
    position: absolute; left: 0; right: 0; top: 298px; text-align: center;
    color: var(--paper); font-size: 14px; letter-spacing: 4px; font-weight: 600;
  }
  .card--back .site em { font-style: normal; color: var(--brand-red); }

  /* Front */
  .card--front { top: 510px; background: var(--paper); }
  .front__band {
    position: absolute; left: 0; top: 0; bottom: 0; width: 92px;
    background: linear-gradient(180deg, var(--brand-red) 0%, var(--brand-red-deep) 100%);
  }
  .front__rule {
    position: absolute; left: 104px; top: 22px; bottom: 0; width: 3px; background: var(--ink);
  }
  .card--front .wordmark {
    left: 132px; top: 44px; transform: none; gap: 14px;
  }
  .card--front .wordmark__square { width: 34px; height: 34px; }
  .card--front .wordmark__name { color: var(--ink); font-size: 24px; }

  .contact { position: absolute; left: 132px; top: 128px; list-style: none; }
  .contact__item {
    display: flex; align-items: center; gap: 9px;
    font-size: 15px; color: var(--ink); margin-bottom: 7px;
  }
  .contact__icon { width: 15px; height: 15px; flex: none; }
  .address {
    position: absolute; left: 132px; top: 236px;
    font-size: 15px; line-height: 1.35; color: var(--ink); font-style: normal;
  }
  .person { position: absolute; right: 44px; bottom: 70px; text-align: right; }
  .person__name {
    font-weight: 800; font-size: 21px; letter-spacing: .5px;
    color: var(--brand-red); text-transform: uppercase;
  }
  .person__role {
    font-size: 14px; letter-spacing: 1.5px; color: var(--muted); text-transform: uppercase;
  }
</style>
</head>
<body>
<main class="stage">

  <section class="card card--back" aria-label="Card back">
    <div class="wordmark">
      <span class="wordmark__square"></span>
      <span class="wordmark__name">Kelbrath Brannock Legal</span>
    </div>
    <p class="site">www.<em>kbtlaw</em>.co</p>
  </section>

  <section class="card card--front" aria-label="Card front">
    <div class="front__band"></div>
    <div class="front__rule"></div>

    <div class="wordmark">
      <span class="wordmark__square"></span>
      <span class="wordmark__name">Kelbrath Brannock Legal</span>
    </div>

    <ul class="contact">
      <li class="contact__item">
        <svg class="contact__icon" viewBox="0 0 16 16" aria-hidden="true"><rect x="4" y="1" width="8" height="14" rx="1.5" fill="none" stroke="#f04a50" stroke-width="1.6"/><circle cx="8" cy="12.3" r="0.9" fill="#f04a50"/></svg>
        0461 738 524
      </li>
      <li class="contact__item">
        <svg class="contact__icon" viewBox="0 0 16 16" aria-hidden="true"><rect x="1" y="3" width="14" height="10" rx="1" fill="#f04a50"/><path d="M1.5 3.8 8 9l6.5-5.2" fill="none" stroke="#fff" stroke-width="1.2"/></svg>
        doran@kbtlaw.co
      </li>
      <li class="contact__item">
        <svg class="contact__icon" viewBox="0 0 16 16" aria-hidden="true"><circle cx="8" cy="8" r="6.5" fill="none" stroke="#f04a50" stroke-width="1.5"/><ellipse cx="8" cy="8" rx="2.8" ry="6.5" fill="none" stroke="#f04a50" stroke-width="1.2"/><path d="M1.5 8h13" stroke="#f04a50" stroke-width="1.2"/></svg>
        www.kbtlaw.co
      </li>
    </ul>

    <address class="address">
      Level 3, 118 Wendmore Street<br>
      Sydney NSW 2000
    </address>

    <div class="person">
      <p class="person__name">Doran Kelbrath</p>
      <p class="person__role">Partner</p>
    </div>
  </section>

</main>
</body>
</html>
```